The Visual Personality of Miss Cobbler Food Trailer

Something that stands out with color and our logo. This is a food trailer that attends several events in the spring and summer. We are known for being one of the best Gumbo producers in mid Michigan. We have been responsible for connecting different communities and cultures together and we are strong supporters of our veterans since this is a veteran owned business. All of our vegetables are fresh and locally purchased. These recipes are originally from New Orleans Louisiana. Our website is Misscobbler.net. This will be used for an 8" x 11" poster. Leave a box or area that states "WHERE WE WILL BE:" so that we can add the location of the event that we are attending.

Target Market(s)

We do cuisine that is recognized in the southern states of the USA. but live in the northern part of the USA. We are providing a menu of different southern recipes so they do not have to go all the way down south for get..

Industry/Entity Type

Food/Restaurant Industry

Font styles to use
Serif
Decorative

Colors
0094D4
00A9DD
6FCCEA
C7EBF8
E9F6FB
59FF00
82FF00
B8FF75
E3FFCB
F4FFEA
FFF300
FFF600
FEFA6F
FFFEC7
FFFEE8
EE7325
F08F49
F5BC92
FAE3D3
FDF4ED
EB3D1F
EC4F4E
F09395
F8D3D4
FCEDEE
A7469A
B969AE
D3A5CF
EDDBEB
F8F0F9

Requirements
Must have
• Our logo, which is "Miss Cobbler", "Homemade Deliciousness". We need an area on the poster where we can manually add the location of the event we will be attending because it changes weekly. location
Nice to have
• Bold colors and logo

```html
<!DOCTYPE html>
<html lang="en">
<head>
<meta charset="utf-8">
<title>Miss Cobbler Food Trailer – Posters</title>
<link rel="stylesheet" href="https://fonts.googleapis.com/css2?family=Bree+Serif&family=Roboto+Slab:wght@500&family=Montserrat:wght@600;800&display=swap">
<style>
  :root{
    --backdrop:#e4e4e4;
    --poster-yellow:#f1d255;
    --poster-yellow-deep:#e3bf3c;
    --ring-red:#e0262f;
    --ring-yellow:#f6d44b;
    --brand-red:#c8202c;
    --ink:#3b3324;
    --placeholder-pink:#e3a9ad;
    --box-white:#f1efee;
    --title-green:#1f5c34;
    --title-red:#b3202a;
    --url-magenta:#b2284c;
    --photo-soup-a:#d9823f;
    --photo-soup-b:#b8452a;
    --photo-bread-a:#e2b274;
    --photo-bread-b:#b96a3a;
  }
  *{margin:0;padding:0;box-sizing:border-box;}
  html,body{width:1200px;height:848px;overflow:hidden;background:var(--backdrop);}
  .canvas{position:relative;width:1200px;height:848px;}

  .poster{position:absolute;top:54px;width:480px;height:740px;overflow:hidden;
    box-shadow:0 10px 30px rgba(0,0,0,.18);}
  .poster--flyer{left:90px;background:linear-gradient(160deg,#efcb45 0%,var(--poster-yellow) 55%,#f5db6a 100%);}
  .poster--cover{left:630px;background:linear-gradient(165deg,var(--poster-yellow-deep) 0%,#e9c94a 55%,#f4d968 100%);}

  /* photo medallions */
  .medallion{position:absolute;border-radius:50%;background:var(--ring-red);}
  .medallion__ring{position:absolute;inset:14%;border-radius:50%;background:var(--ring-yellow);}
  .medallion__photo{position:absolute;inset:16.5%;border-radius:50%;}
  .photo--soup{background:radial-gradient(circle at 45% 50%,var(--photo-soup-a),var(--photo-soup-b) 70%,#cfcac2 72%);}
  .photo--shrimp{background:radial-gradient(circle at 50% 50%,#e6b58a,#c2613e 70%);}
  .photo--sandwich{background:linear-gradient(150deg,#efe4c9 0%,var(--photo-bread-a) 45%,var(--photo-bread-b) 100%);}
  .photo--burger{background:linear-gradient(170deg,#5a3a26 0%,var(--photo-bread-a) 55%,#8a6a3a 100%);}

  .medallion--top{left:-30px;top:-5px;width:250px;height:250px;}
  .medallion--mid{left:-67px;top:298px;width:194px;height:194px;}
  .medallion--bottom-left{left:-10px;top:560px;width:210px;height:210px;}
  .medallion--bottom-right{left:355px;top:570px;width:140px;height:140px;}

  .garnish{position:absolute;border-radius:50%;}
  .garnish--herb{left:112px;top:255px;width:55px;height:80px;background:radial-gradient(ellipse,#5f9a3a,rgba(95,154,58,0) 70%);}
  .garnish--pepper{left:70px;top:490px;width:100px;height:35px;background:linear-gradient(100deg,#e58a2f,#f2b04a);border-radius:40px;}
  .garnish--pepper-ring{left:395px;top:505px;width:60px;height:55px;background:radial-gradient(circle,#a9d46a,rgba(169,212,106,0) 70%);}

  .brand{position:absolute;left:285px;top:70px;width:180px;text-align:center;}
  .brand__dot{display:block;width:16px;height:16px;border-radius:50%;background:var(--brand-red);margin:0 auto 10px;}
  .brand__name{font-family:"Bree Serif",serif;color:var(--brand-red);font-size:38px;line-height:1.02;}
  .brand__tagline{margin-top:10px;font-family:"Bree Serif",serif;color:var(--ink);font-size:12px;letter-spacing:.5px;text-transform:uppercase;}

  .about{position:absolute;left:178px;top:298px;width:272px;font-family:"Roboto Slab",serif;font-weight:500;
    font-size:10.3px;line-height:19px;letter-spacing:1.4px;text-transform:uppercase;color:var(--ink);text-align:justify;}

  .location-box{position:absolute;left:166px;top:424px;width:290px;height:112px;background:var(--box-white);
    border-radius:14px;padding:26px 18px 0;}
  .location-box__label{font-family:"Bree Serif",serif;color:var(--brand-red);font-size:14.5px;letter-spacing:.6px;}
  .location-box__placeholder{margin-top:16px;margin-left:34px;font-family:"Roboto Slab",serif;color:var(--placeholder-pink);
    font-size:13.5px;letter-spacing:2.2px;}

  .schedule{position:absolute;left:160px;top:552px;width:240px;text-align:center;font-family:"Bree Serif",serif;
    color:var(--brand-red);font-size:15px;line-height:23px;}

  .cover-title{position:absolute;left:60px;top:150px;font-family:"Montserrat",sans-serif;font-weight:800;
    font-size:66px;line-height:.95;letter-spacing:-2px;}
  .cover-title__line{display:block;color:var(--title-green);}
  .cover-title__line--accent{color:var(--title-red);}
  .cover-url{position:absolute;left:0;right:0;top:660px;text-align:center;font-family:"Montserrat",sans-serif;
    font-weight:600;font-size:16px;color:var(--url-magenta);}
</style>
</head>
<body>
<main class="canvas">

  <section class="poster poster--flyer" aria-label="Miss Cobbler flyer">
    <div class="medallion medallion--top"><div class="medallion__ring"></div>
      <div class="medallion__photo photo--soup" role="img" aria-label="Bowl of gumbo"></div></div>
    <div class="medallion medallion--mid"><div class="medallion__ring"></div>
      <div class="medallion__photo photo--shrimp" role="img" aria-label="Shrimp and tomato dish"></div></div>
    <div class="medallion medallion--bottom-left"><div class="medallion__ring"></div>
      <div class="medallion__photo photo--sandwich" role="img" aria-label="Po' boy sandwich with chips"></div></div>
    <div class="medallion medallion--bottom-right"><div class="medallion__ring"></div>
      <div class="medallion__photo photo--burger" role="img" aria-label="Fried sandwich with pickles"></div></div>

    <div class="garnish garnish--herb" role="img" aria-label="Cilantro sprigs"></div>
    <div class="garnish garnish--pepper" role="img" aria-label="Chili peppers"></div>
    <div class="garnish garnish--pepper-ring" role="img" aria-label="Green pepper rings"></div>

    <div class="brand">
      <span class="brand__dot"></span>
      <p class="brand__name">Miss<br>Cobbler</p>
      <p class="brand__tagline">Homemade Deliciousness!</p>
    </div>

    <p class="about">We prepare and serve amazing high quality, delicious southern food at an affordable price. We want to provide our customers with the most authentic Louisiana experience outside of Louisiana.</p>

    <div class="location-box">
      <p class="location-box__label">WHERE WE WILL BE</p>
      <p class="location-box__placeholder">YOUR ADDRESS HERE</p>
    </div>

    <p class="schedule">Monday, Friday, Saturday<br>11:00 am EST - 3 pm EST</p>
  </section>

  <section class="poster poster--cover" aria-label="Miss Cobbler Trailer cover">
    <h1 class="cover-title">
      <span class="cover-title__line">MISS</span>
      <span class="cover-title__line">COBBLER</span>
      <span class="cover-title__line cover-title__line--accent">TRAILER</span>
    </h1>
    <p class="cover-url">www.misscobbler.net</p>
  </section>

</main>
</body>
</html>
```